PlayTallyCollective - Game Statistics and Achievement Tracking

I need a new modern design for an existing website.

The website is a project to track statistics and achievements for games (currently Vaporn Achievements/Stats and stats for Cargo Haul Odyssey 2 and Frontier Rig Journeys).
I am currently expanding the site with other platforms (like QVR) and more games.
I am also adding a user registration/signin with user profiles to show off their achievements and stats across all platforms and games.

The current website is available at https://plytly.example/
To search for data you can use the username "pixelornin" (without quotes).

The design should be modern and extendable and contain space for a logo.

The logo should match the project. It should combine Gaming with statistics.

Target Market(s)

Video game players

Number of Pages Required

5+ page

Font styles to use
Sans Serif

Requirements
Must have
• Basic Layout, User profile page (not yet available on live site), Search Page for Platforms/Games, Platform profile page, Dark theme

```html
<!DOCTYPE html>
<html lang="en">
<head>
<meta charset="utf-8">
<title>PlayTallyCollective – Game Statistics and Achievement Tracking</title>
<link href="https://fonts.googleapis.com/css2?family=Poppins:wght@400;500;600;700&display=swap" rel="stylesheet">
<style>
:root{
  --bg:#202020;
  --bg-dark:#161616;
  --cyan:#17c9cc;
  --orange:#ea5410;
  --orange-2:#f26f1f;
  --text:#ffffff;
  --muted:#cfcfcf;
  --green:#3ad13a;
  --card-border:#585858;
}
*{box-sizing:border-box;margin:0;padding:0}
html,body{width:1200px;height:3205px;overflow:hidden}
body{background:var(--bg);color:var(--text);font-family:'Poppins',sans-serif;position:relative}
.abs{position:absolute}

/* header */
.site-header{position:absolute;left:0;top:0;width:1200px;height:82px;background:#1a1a1a;z-index:3}
.brand{position:absolute;left:75px;top:30px;display:flex;align-items:center;gap:9px;font-weight:600;font-size:17px;letter-spacing:.3px}
.brand-mark{width:14px;height:14px;background:var(--cyan)}
.main-nav a{position:absolute;top:33px;font-size:14px;font-weight:600;color:#fff;text-decoration:none}
.main-nav a.active{color:var(--cyan)}
.btn{display:flex;align-items:center;justify-content:center;background:linear-gradient(90deg,var(--orange),var(--orange-2));color:#fff;font-weight:600;border-radius:30px;text-decoration:none}
.btn-signin{position:absolute;left:976px;top:22px;width:151px;height:38px;font-size:13px}

/* hero */
.hero-bg{position:absolute;left:0;top:82px;width:1200px;height:639px;border-radius:0 0 50% 50% / 0 0 80px 80px;
  background:radial-gradient(ellipse at 82% 30%,#6a5a22 0%,rgba(60,50,30,0) 45%),radial-gradient(ellipse at 20% 40%,#4a3a2c 0%,rgba(0,0,0,0) 50%),linear-gradient(180deg,#2c2824 0%,#1a1815 100%)}
.search-bar{position:absolute;left:184px;top:175px;width:832px;height:53px;border:2px solid #d9d9d9;border-radius:30px;background:rgba(20,20,20,.55)}
.search-bar span{position:absolute;left:27px;top:16px;font-size:14px;color:#eaeaea}
.search-btn{position:absolute;right:8px;top:7px;width:36px;height:36px;border-radius:50%;background:var(--cyan);display:flex;align-items:center;justify-content:center}
.profile-card{position:absolute;left:187px;top:245px;width:828px;height:390px;border:1px solid #8a8a8a;border-radius:18px;background:rgba(14,14,14,.72)}
.avatar{position:absolute;left:18px;top:32px;width:194px;height:266px;border-radius:14px;overflow:hidden;background:linear-gradient(160deg,#e8c89a 0%,#7fb6d6 60%,#4a7aa0 100%)}
.avatar-name{position:absolute;left:0;bottom:0;width:100%;height:62px;background:var(--cyan);display:flex;align-items:center;justify-content:center;font-size:22px;font-weight:600}
.badge{position:absolute;top:316px;width:42px;height:42px;border:1px solid #bdbdbd;border-radius:50%;display:flex;align-items:center;justify-content:center;font-size:13px}
.flag{background:linear-gradient(180deg,#111 0 33%,#dd0000 33% 66%,#ffce00 66%);border:none}
.profile-title{position:absolute;left:241px;top:35px;font-size:25px;font-weight:600}
.stat-row{position:absolute;left:241px;font-size:15px;font-weight:600;display:flex;width:560px}
.stat-row .label{width:200px}
.stat-row svg{margin:0 12px 0 9px;flex:none}
.action{position:absolute;top:316px;width:42px;height:42px;border:1px solid #bdbdbd;border-radius:50%;display:flex;align-items:center;justify-content:center}

/* statistics */
.section-title{position:absolute;font-weight:700;font-size:42px;text-align:center}
.stat-card{position:absolute;width:330px;height:219px;border:1px solid var(--card-border);border-radius:12px;background:linear-gradient(180deg,#0c0c0c 0%,#3c3c3c 100%);text-align:center}
.stat-card svg{position:absolute;left:50%;top:28px;transform:translateX(-50%)}
.stat-card .num{position:absolute;left:0;top:114px;width:100%;font-size:43px;font-weight:700;color:var(--cyan);line-height:1}
.stat-card .num.small{top:122px;font-size:21px;line-height:28px}
.stat-card .lbl{position:absolute;left:0;top:168px;width:100%;font-size:16px}
.stat-card .lbl.low{top:180px}

/* about */
.about-bg{position:absolute;left:0;top:1658px;width:1200px;height:452px;background:radial-gradient(ellipse at 50% 100%,#4a2c8a 0%,rgba(40,30,90,0) 55%),radial-gradient(ellipse at 15% 40%,#1e3a6a 0%,rgba(0,0,0,0) 45%),linear-gradient(180deg,#161a2a 0%,#1c1a3a 100%)}
.about-text{position:absolute;left:130px;top:1788px;width:940px;font-size:15px;line-height:32px;text-align:center}
.about-text p+p{margin-top:10px}
.btn-learn{position:absolute;left:513px;top:1985px;width:173px;height:54px;font-size:16px}

/* featured */
.arrow{position:absolute;width:28px;height:28px;border-radius:50%;display:flex;align-items:center;justify-content:center}
.arrow.light{background:#fff}
.arrow.cyan{background:var(--cyan)}
.game-card{position:absolute;top:2235px;width:243px;height:171px;border:1px solid var(--card-border);border-radius:8px;background:#1b1b1b;overflow:hidden}
.game-thumb{height:92px}
.game-card h3{position:absolute;left:15px;top:106px;font-size:17px;font-weight:600}
.game-card .pct{position:absolute;right:16px;top:109px;font-size:14px;color:var(--green)}
.game-card .meta{position:absolute;left:15px;top:137px;font-size:14px;word-spacing:14px}

/* profiles */
.profiles-bg{position:absolute;left:0;top:2478px;width:1200px;height:565px;background:radial-gradient(ellipse at 50% 30%,#2c2a4a 0%,rgba(0,0,0,0) 60%),linear-gradient(180deg,#1e2030 0%,#17171c 100%)}
.user-highlight{position:absolute;left:330px;top:2683px;width:272px;height:294px;border-radius:24px;background:linear-gradient(180deg,#222 0%,#444 100%)}
.user{position:absolute;top:2615px;width:260px;text-align:center}
.user-photo{width:160px;height:160px;border-radius:50%;margin:0 auto;border:2px solid #dcdcdc}
.user h3{font-size:23px;font-weight:600;margin-top:18px;line-height:30px}
.user p{font-size:13px;color:var(--muted);line-height:24px}
.user p.gap{margin-top:6px}
.btn-more{width:110px;height:37px;margin:10px auto 0;font-size:13px}

/* footer */
.site-footer{position:absolute;left:0;top:3043px;width:1200px;height:162px;background:#1a1a1a}
.footer-nav a{position:absolute;top:58px;font-size:16px;font-weight:600;color:#fff;text-decoration:none}
.copyright{position:absolute;left:75px;top:102px;font-size:13px;color:#ddd}
.social{position:absolute;right:73px;top:80px;display:flex;gap:14px;font-size:13px;font-weight:600}
</style>
</head>
<body>

<header class="site-header">
  <div class="brand"><span class="brand-mark"></span>PLAYTALLYCOLLECTIVE</div>
  <nav class="main-nav">
    <a href="#" class="active" style="left:506px">Home</a>
    <a href="#" style="left:589px">About Us</a>
    <a href="#" style="left:695px">Games</a>
    <a href="#" style="left:785px">Vaporn</a>
    <a href="#" style="left:876px">Contact</a>
  </nav>
  <a href="#" class="btn btn-signin">Register/Sign in</a>
</header>

<div class="hero-bg" role="img" aria-label="Dim photo of a heavy truck on a highway at dusk"></div>

<div class="search-bar">
  <span>Search Platforms/Games</span>
  <div class="search-btn"><svg width="14" height="14" viewBox="0 0 14 14"><circle cx="6" cy="6" r="4" fill="none" stroke="#111" stroke-width="2"/><path d="M9 9l3.5 3.5" stroke="#111" stroke-width="2"/></svg></div>
</div>

<section class="profile-card">
  <div class="avatar" role="img" aria-label="Cartoon avatar of the player">
    <div class="avatar-name">pixelornin</div>
  </div>
  <div class="badge" style="left:18px">179</div>
  <div class="badge" style="left:69px">15</div>
  <div class="badge" style="left:120px">87</div>
  <div class="badge flag" style="left:170px" role="img" aria-label="Country flag"></div>

  <h2 class="profile-title">pixelornin</h2>
  <div class="stat-row" style="top:86px"><span class="label">Played Games:</span><svg width="16" height="16" viewBox="0 0 16 16"><g fill="#17c9cc"><rect x="1" y="2" width="3" height="2"/><rect x="6" y="2" width="9" height="2"/><rect x="1" y="7" width="3" height="2"/><rect x="6" y="7" width="9" height="2"/><rect x="1" y="12" width="3" height="2"/><rect x="6" y="12" width="9" height="2"/></g></svg>1166 / 1644 (70%)</div>
  <div class="stat-row" style="top:123px"><span class="label">Total play time:</span><svg width="16" height="16" viewBox="0 0 16 16"><circle cx="8" cy="8" r="7" fill="#17c9cc"/><path d="M8 4v4l3 2" stroke="#111" stroke-width="1.6" fill="none"/></svg>1 year 2 months 11 hours 25 minutes</div>
  <div class="stat-row" style="top:160px"><span class="label">Achievements:</span><svg width="16" height="16" viewBox="0 0 16 16"><path d="M2 10l6-8h6v6l-8 6z" fill="#17c9cc"/><circle cx="11" cy="5" r="1.3" fill="#111"/></svg>18007 / 63070 (28%)</div>
  <div class="stat-row" style="top:198px"><span class="label">Member since:</span><svg width="16" height="16" viewBox="0 0 16 16"><rect x="1" y="3" width="14" height="12" rx="1" fill="#17c9cc"/><rect x="3" y="7" width="10" height="6" fill="#111" opacity=".4"/></svg>14.01.2009</div>
  <div class="stat-row" style="top:236px"><span class="label">Last played:</span><svg width="16" height="16" viewBox="0 0 16 16"><circle cx="8" cy="8" r="6.5" fill="none" stroke="#17c9cc" stroke-width="1.5"/><path d="M1.5 8h13M8 1.5c3 3 3 10 0 13M8 1.5c-3 3-3 10 0 13" stroke="#17c9cc" fill="none"/></svg>Rail Route Worlds® 5</div>
  <div class="stat-row" style="top:273px"><span class="label">Last Update:</span><svg width="16" height="16" viewBox="0 0 16 16"><path d="M6 3L1 7l5 4V8c4 0 6 1 8 5 0-5-3-8-8-8z" fill="#17c9cc"/></svg>26.12.2024 16:00h</div>

  <div class="action" style="left:631px"><svg width="16" height="16" viewBox="0 0 16 16" fill="none" stroke="#fff" stroke-width="1.8"><path d="M13 6a5 5 0 0 0-9-1M3 10a5 5 0 0 0 9 1"/><path d="M4 2v3h3M12 14v-3H9"/></svg></div>
  <div class="action" style="left:682px"><svg width="16" height="16" viewBox="0 0 16 16"><path d="M3 13l5-5M9 3l4 4-3 3-4-4z" stroke="#fff" stroke-width="2" fill="#fff"/></svg></div>
  <div class="action" style="left:732px"><svg width="14" height="16" viewBox="0 0 14 16" fill="#fff"><ellipse cx="7" cy="3" rx="6" ry="2.5"/><path d="M1 5c0 3 12 3 12 0v3c0 3-12 3-12 0zM1 10c0 3 12 3 12 0v3c0 3-12 3-12 0z"/></svg></div>
  <div class="action" style="left:783px"><svg width="14" height="15" viewBox="0 0 14 15"><rect x="1" y="2" width="12" height="12" fill="#fff"/><g fill="#222"><rect x="3" y="6" width="2" height="2"/><rect x="6" y="6" width="2" height="2"/><rect x="9" y="6" width="2" height="2"/><rect x="3" y="10" width="2" height="2"/><rect x="6" y="10" width="2" height="2"/><rect x="9" y="10" width="2" height="2"/></g></svg></div>
</section>

<!-- statistics -->
<h2 class="section-title" style="left:0;top:788px;width:1200px">Statistics</h2>

<div class="stat-card" style="left:75px;top:875px">
  <svg width="104" height="70" viewBox="0 0 104 70" fill="none" stroke="#ea5410" stroke-width="4"><path d="M22 6h60c14 0 20 28 20 48 0 10-10 14-18 6l-10-12H30L20 60c-8 8-18 4-18-6C2 34 8 6 22 6z"/><path d="M30 22v16M22 30h16"/><circle cx="70" cy="24" r="3"/><circle cx="78" cy="32" r="3"/><circle cx="62" cy="32" r="3"/><circle cx="70" cy="40" r="3"/></svg>
  <div class="num">251966</div><div class="lbl">Games</div>
</div>
<div class="stat-card" style="left:435px;top:875px">
  <svg width="62" height="74" viewBox="0 0 62 74" fill="none" stroke="#ea5410" stroke-width="3"><path d="M31 3l7 6 9-1 2 9 8 5-4 8 4 8-8 5-2 9-9-1-7 6-7-6-9 1-2-9-8-5 4-8-4-8 8-5 2-9 9 1z"/><circle cx="31" cy="31" r="12"/><path d="M18 55l-6 16 9-4 5 6 5-14M44 55l6 16-9-4-5 6-5-14"/></svg>
  <div class="num">2692707</div><div class="lbl">Game Achievements</div>
</div>
<div class="stat-card" style="left:797px;top:875px">
  <svg width="72" height="74" viewBox="0 0 72 74" fill="none" stroke="#ea5410" stroke-width="3"><path d="M4 72h66"/><rect x="8" y="50" width="8" height="22"/><rect x="22" y="42" width="8" height="30"/><rect x="36" y="34" width="8" height="38"/><rect x="50" y="24" width="8" height="48"/><rect x="62" y="14" width="6" height="58"/><path d="M10 36l14-10 14 4 14-14 12-12"/><circle cx="64" cy="4" r="3"/></svg>
  <div class="num">339284</div><div class="lbl">Game Stats</div>
</div>

<div class="stat-card" style="left:75px;top:1120px">
  <svg width="78" height="78" viewBox="0 0 78 78" fill="none" stroke="#ea5410" stroke-width="3.5"><circle cx="39" cy="41" r="34"/><circle cx="39" cy="41" r="26"/><path d="M39 41l-9-12M39 41l13-8"/><path d="M58 6l8 2-2 8"/></svg>
  <div class="num">3271530</div><div class="lbl">Playtime Records</div>
</div>
<div class="stat-card" style="left:435px;top:1120px">
  <svg width="78" height="78" viewBox="0 0 78 78" fill="none" stroke="#ea5410" stroke-width="3"><rect x="3" y="3" width="72" height="72"/><rect x="10" y="10" width="58" height="58"/><circle cx="39" cy="28" r="10"/><path d="M22 48c4-10 30-10 34 0"/><rect x="16" y="52" width="46" height="8"/><path d="M70 10v20"/></svg>
  <div class="num">1033</div><div class="lbl">Public Profiles</div>
</div>
<div class="stat-card" style="left:797px;top:1120px">
  <svg width="60" height="74" viewBox="0 0 60 74" fill="none" stroke="#ea5410" stroke-width="3"><path d="M26 4h22l-2 16c-2 8-16 8-18 0z"/><path d="M26 8h-6c0 8 4 12 8 12M48 8h6c0 8-4 12-8 12M37 26v8M30 36h14"/><path d="M6 58l14-14 12 4 10 8-6 6-10-4M6 58l12 14M2 62l12 12"/></svg>
  <div class="num">21087125</div><div class="lbl">User Achievements</div>
</div>

<div class="stat-card" style="left:75px;top:1363px">
  <svg width="80" height="78" viewBox="0 0 80 78" fill="none" stroke="#ea5410" stroke-width="3"><path d="M6 34l16-14 18 8 18-18 16-4"/><circle cx="6" cy="34" r="4"/><circle cx="22" cy="20" r="4"/><circle cx="40" cy="28" r="4"/><circle cx="74" cy="6" r="4"/><circle cx="20" cy="54" r="6"/><circle cx="40" cy="52" r="6"/><circle cx="60" cy="54" r="6"/><path d="M8 76c0-12 24-12 24 0M28 76c0-14 24-14 24 0M48 76c0-12 24-12 24 0"/></svg>
  <div class="num">2552885</div><div class="lbl">User Stats</div>
</div>
<div class="stat-card" style="left:435px;top:1363px">
  <svg width="104" height="78" viewBox="0 0 104 78" fill="none" stroke="#ea5410" stroke-width="3.5"><rect x="18" y="6" width="68" height="46" rx="6"/><path d="M14 30c-8 8-8 24 2 34l6 12M90 30c8 8 8 24-2 34l-6 12"/><path d="M26 26l8 16M78 26l-8 16"/><path d="M46 30h6v-6h6v6h6v6h-6v6h-6v-6h-6z" fill="#ea5410" stroke="none"/><circle cx="46" cy="16" r="2.5"/></svg>
  <div class="num">2276964</div><div class="lbl">Owned Games</div>
</div>
<div class="stat-card" style="left:797px;top:1363px">
  <svg width="76" height="78" viewBox="0 0 76 78" fill="none" stroke="#ea5410" stroke-width="3.5"><rect x="3" y="10" width="70" height="64" rx="4"/><path d="M3 24h70M16 3v12M30 3v12M46 3v12M60 3v12"/><rect x="14" y="34" width="10" height="9"/><rect x="33" y="34" width="10" height="9"/><rect x="52" y="34" width="10" height="9"/><rect x="14" y="53" width="10" height="9"/><rect x="33" y="53" width="10" height="9"/><rect x="52" y="53" width="10" height="9"/></svg>
  <div class="num small">2932 years 8 months 1 day<br>19 hours 43 minutes</div><div class="lbl low">Total Playtime</div>
</div>

<!-- about -->
<div class="about-bg" role="img" aria-label="Neon futuristic city street background"></div>
<h2 class="section-title" style="left:0;top:1718px;width:1200px">About PlayTallyCollective</h2>
<div class="about-text">
  <p>The PlayTallyCollective, short PTally or P-Tally, was established in August 2012 as a website providing game statistics for the Syndicate 2 Multiplayer Modification, that was work in progress back in the date and has sadly been canceled some years later, and Blockcraft with a custom Blokkit plugin.</p>
  <p>After the Syndicate 2 Multiplayer Modification had been cancelled and Blokkit has been shutdown the network moved on to provide game time and achievement statistics for Vaporn.</p>
</div>
<a href="#" class="btn btn-learn">Learn More</a>

<!-- featured -->
<h2 class="section-title" style="left:75px;top:2160px">Featured Games</h2>
<div class="arrow light" style="left:1055px;top:2175px"><svg width="12" height="12" viewBox="0 0 12 12"><path d="M8 1L3 6l5 5" stroke="#111" stroke-width="2.6" fill="none"/></svg></div>
<div class="arrow cyan" style="left:1098px;top:2175px"><svg width="12" height="12" viewBox="0 0 12 12"><path d="M4 1l5 5-5 5" stroke="#111" stroke-width="2.6" fill="none"/></svg></div>

<article class="game-card" style="left:75px">
  <div class="game-thumb" role="img" aria-label="Game cover art" style="background:linear-gradient(120deg,#e9e4dc 0%,#b9b3a8 55%,#3a4a8a 80%,#d4a020 100%)"></div>
  <h3>Lunar Passage</h3><span class="pct">100%</span><div class="meta">5h 1/1</div>
</article>
<article class="game-card" style="left:344px">
  <div class="game-thumb" role="img" aria-label="Game cover art" style="background:linear-gradient(120deg,#2a1010 0%,#8a1a1a 45%,#3a2a2a 100%)"></div>
  <h3>Lunar Passage</h3><span class="pct">100%</span><div class="meta">5h 1/1</div>
</article>
<article class="game-card" style="left:618px">
  <div class="game-thumb" role="img" aria-label="Game cover art" style="background:linear-gradient(120deg,#3a1a7a 0%,#2ac0d0 50%,#8a2aa0 100%)"></div>
  <h3>Lunar Passage</h3><span class="pct">100%</span><div class="meta">5h 1/1</div>
</article>
<article class="game-card" style="left:884px">
  <div class="game-thumb" role="img" aria-label="Game cover art" style="background:linear-gradient(120deg,#1a2a3a 0%,#5a6a7a 45%,#8a1010 100%)"></div>
  <h3>Lunar Passage</h3><span class="pct">100%</span><div class="meta">5h 1/1</div>
</article>

<!-- profiles -->
<div class="profiles-bg" role="img" aria-label="Dim gaming room background"></div>
<h2 class="section-title" style="left:0;top:2518px;width:1200px">User Profiles</h2>
<div class="arrow light" style="left:30px;top:2839px"><svg width="12" height="12" viewBox="0 0 12 12"><path d="M8 1L3 6l5 5" stroke="#111" stroke-width="2.6" fill="none"/></svg></div>
<div class="arrow cyan" style="left:1141px;top:2839px"><svg width="12" height="12" viewBox="0 0 12 12"><path d="M4 1l5 5-5 5" stroke="#111" stroke-width="2.6" fill="none"/></svg></div>
<div class="user-highlight"></div>

<div class="user" style="left:65px">
  <div class="user-photo" role="img" aria-label="Player portrait photo" style="background:linear-gradient(160deg,#5a3aa0,#d0a020)"></div>
  <h3>User Name</h3><p>Member since: 14.01.2009</p><p class="gap">Total play time:</p><p>1 year 2 months 11 hours 25 minutes</p>
  <a href="#" class="btn btn-more">More Info</a>
</div>
<div class="user" style="left:334px">
  <div class="user-photo" role="img" aria-label="Player portrait photo" style="background:linear-gradient(160deg,#4a5a6a,#1a2028)"></div>
  <h3>User Name</h3><p>Member since: 14.01.2009</p><p class="gap">Total play time:</p><p>1 year 2 months 11 hours 25 minutes</p>
  <a href="#" class="btn btn-more">More Info</a>
</div>
<div class="user" style="left:607px">
  <div class="user-photo" role="img" aria-label="Player portrait photo" style="background:linear-gradient(160deg,#c02a2a,#6a3ac0)"></div>
  <h3>User Name</h3><p>Member since: 14.01.2009</p><p class="gap">Total play time:</p><p>1 year 2 months 11 hours 25 minutes</p>
  <a href="#" class="btn btn-more">More Info</a>
</div>
<div class="user" style="left:876px">
  <div class="user-photo" role="img" aria-label="Player portrait photo" style="background:linear-gradient(160deg,#2a2a3a,#c02020)"></div>
  <h3>User Name</h3><p>Member since: 14.01.2009</p><p class="gap">Total play time:</p><p>1 year 2 months 11 hours 25 minutes</p>
  <a href="#" class="btn btn-more">More Info</a>
</div>

<!-- footer -->
<footer class="site-footer">
  <nav class="footer-nav">
    <a href="#" style="left:75px">Home</a>
    <a href="#" style="left:175px">About Us</a>
    <a href="#" style="left:301px">Games</a>
    <a href="#" style="left:412px">Vaporn</a>
    <a href="#" style="left:519px">Contact</a>
  </nav>
  <p class="copyright">Copyright © 2024 Company Name. All right reserved.</p>
  <div class="social"><span>Friendly</span><span>Chirper</span><span>Photoly</span><span>Careerly</span><span>Clipcast</span></div>
</footer>

</body>
</html>
```